Business Card for Coastal Tundrabridge Advisory

We need a business card for Coastal Tundrabridge Advisory. The company website address is provided below. The company logo is attached. We provide specialized permafrost services to the mining, transportation, and oil & gas industries. The card should be prepared for:
Matthias Korhonen, PhD.
Coastal Tundrabridge Advisory
PO Box 418259
Quillwater, Alaska 99642
Direct: +1-907-555-0143
Email: mkorhonen@tundrabridgeadvisory.example
Website: www.coastaltundrabridgeadvisory.example

```html
<!DOCTYPE html>
<html lang="en">
<head>
<meta charset="utf-8">
<title>Coastal Tundrabridge Advisory – Business Card</title>
<link href="https://fonts.googleapis.com/css2?family=Montserrat:wght@400;600;700&display=swap" rel="stylesheet">
<style>
  :root {
    --backdrop: #9c9c9c;
    --ink: #121923;
    --ink-soft: #2a2f36;
    --paper: #ffffff;
    --emboss: #1e2631;
  }
  * { margin: 0; padding: 0; box-sizing: border-box; }
  html, body { width: 1200px; height: 1059px; overflow: hidden; }
  body {
    background: var(--backdrop);
    font-family: "Montserrat", Arial, sans-serif;
    position: relative;
  }
  .card {
    position: absolute;
    border-radius: 24px;
    overflow: hidden;
  }
  .card--front {
    left: 256px; top: 89px; width: 688px; height: 390px;
    background: var(--ink);
  }
  .front-wordmark {
    position: absolute;
    left: 0; right: 0; top: 168px;
    text-align: center;
    color: var(--emboss);
    font-weight: 700;
    font-size: 34px;
    letter-spacing: 5px;
    text-transform: uppercase;
  }
  .card--back {
    left: 252px; top: 546px; width: 696px; height: 395px;
    background: var(--paper);
    color: var(--ink-soft);
  }
  .back-band {
    position: absolute; left: 0; right: 0; bottom: 0; height: 10px;
    background: var(--ink);
  }
  .back-accent {
    position: absolute; right: 0; top: 171px; width: 11px; height: 51px;
    background: var(--ink);
  }
  .back-wordmark {
    position: absolute; left: 32px; top: 34px;
    color: var(--ink);
    font-weight: 700;
    font-size: 19px;
    letter-spacing: 2px;
    text-transform: uppercase;
  }
  .holder {
    position: absolute; right: 26px; top: 163px; text-align: right;
  }
  .holder__name {
    color: var(--ink); font-weight: 700; font-size: 22px; line-height: 30px;
  }
  .holder__company { font-size: 18px; line-height: 28px; }
  .address {
    position: absolute; left: 31px; top: 206px;
    font-size: 18px; line-height: 28px;
  }
  .contact {
    position: absolute; left: 32px; top: 290px;
    font-size: 18px; line-height: 27px; list-style: none;
  }
  .contact__label { font-weight: 600; color: var(--ink); }
</style>
</head>
<body>
  <section class="card card--front" aria-label="Card front">
    <div class="front-wordmark">Coastal Tundrabridge Advisory</div>
  </section>

  <section class="card card--back" aria-label="Card back">
    <div class="back-wordmark">Coastal Tundrabridge Advisory</div>

    <div class="holder">
      <div class="holder__name">Matthias Korhonen, PhD</div>
      <div class="holder__company">Coastal Tundrabridge Advisory</div>
    </div>
    <div class="back-accent"></div>

    <address class="address" style="font-style:normal">
      PO Box 418259<br>
      Quillwater, Alaska 99642
    </address>

    <ul class="contact">
      <li><span class="contact__label">Direct:</span> +1-907-555-0143</li>
      <li><span class="contact__label">Email:</span> mkorhonen@tundrabridgeadvisory.example</li>
      <li><span class="contact__label">Website:</span> www.coastaltundrabridgeadvisory.example</li>
    </ul>

    <div class="back-band"></div>
  </section>
</body>
</html>
```